A revolutionary website for a revolutionary construction company

I am looking for inspirations... please help me and read the attached brief

I would like to achieve a website design that is modern, premium dynamic and drives emotions. I do not want a design that can be found on a normal template. Having that said, I would also like the utilisation of Illustrations that are relation to the company’s services…. Also would like to have illustrations dynamic when you navigate on them. So a young, dynamic and parallax design website that will show off these requirements. Also to add trust, with all pages designed.

please see attachements.
Updates

Low design quality

Target Market(s)

Please read brief

Number of Pages Required

5+ page

Font styles to use
Other font styles liked:
• Futura

Requirements
Must have
• Please read brief - colours to be matching logo colours
Nice to have
Should not have

```html
<!DOCTYPE html>
<html lang="en">
<head>
<meta charset="utf-8">
<title>Keystone Forma</title>
<link href="https://fonts.googleapis.com/css2?family=Jost:wght@400;500;600;700;800;900&display=swap" rel="stylesheet">
<style>
:root{
  --brand:#8c0033;
  --brand-soft:#b0476b;
  --ink:#222;
  --muted:#555;
  --white:#fff;
  --footer:#0d0d0d;
  --divider:#444;
}
*{box-sizing:border-box;margin:0;padding:0}
html,body{width:1200px;height:3899px;overflow:hidden}
body{position:relative;font-family:'Jost',Arial,sans-serif;color:var(--ink);background:var(--white)}
.abs{position:absolute}

.topbar{left:0;top:0;width:1200px;height:26px;background:var(--brand);color:var(--white);font-size:13px;font-weight:500;padding:4px 62px}
.topbar .social{position:absolute;right:62px;top:6px;display:flex;gap:8px}
.dot{width:13px;height:13px;border-radius:50%;background:var(--white);display:block}

.header{left:0;top:26px;width:1200px;height:105px;background:var(--white)}
.brand{left:80px;top:10px;width:150px;text-align:center}
.brand .mark{width:58px;height:58px;border:2px solid #444;border-radius:50%;margin:0 auto 5px}
.brand .name{font-size:12px;letter-spacing:2px;color:var(--brand);font-weight:500;white-space:nowrap}
.brand .tag{font-size:7px;color:var(--brand)}
.nav{right:86px;top:44px;display:flex;gap:53px;font-size:16px;font-weight:700;color:#111}
.nav .on{color:var(--brand)}

.hero{left:0;top:131px;width:1200px;height:570px;background:linear-gradient(180deg,#2f3340 0%,#4a4f5e 30%,#6e7280 60%,#a3a5ab 85%,#8c8e94 100%)}
.hero h2{position:absolute;top:218px;width:100%;text-align:center;color:var(--white);font-weight:400;font-size:46px;letter-spacing:1px}
.hero h1{position:absolute;top:270px;width:100%;text-align:center;color:var(--brand);font-weight:900;font-size:62px;letter-spacing:2px}

.slide-img{top:643px;height:260px}
.service-card{left:437px;top:643px;width:326px;height:260px;background:var(--brand);border:8px solid #5a5a5a;color:var(--white);text-align:center;padding:14px 26px}
.service-card h3{font-size:20px;font-weight:700;margin:6px 0 6px;letter-spacing:1px}
.service-card p{font-size:13.5px;line-height:21px;font-weight:500}
.arrow{top:759px;width:30px;height:30px;background:var(--brand-soft);display:flex;align-items:center;justify-content:center}

.section-title{font-weight:900;color:var(--brand);font-size:40px;letter-spacing:1px;white-space:nowrap}
.center{width:1200px;left:0;text-align:center}

.about-text{left:61px;top:1052px;width:525px;font-size:15.6px;line-height:21px;color:#333}
.about-text p+p{margin-top:21px}

.btn{border:3px solid var(--brand);color:var(--brand);font-weight:700;font-size:15px;display:flex;align-items:center;justify-content:center;letter-spacing:.5px;background:transparent}

.grid{left:63px;top:1536px;width:1075px;height:481px;display:grid;grid-template-columns:repeat(4,1fr);grid-template-rows:repeat(2,1fr)}
.cell{width:100%;height:100%}
.hosp{background:var(--brand);border:8px solid #7a7a7a;color:var(--white);text-align:center;padding:12px 14px}
.hosp h3{font-size:19px;font-weight:700;margin:6px 0 6px}
.hosp p{font-size:13.5px;line-height:19px;font-weight:500}

.post{top:2264px;width:313px}
.post .ph{height:166px}
.post h3{font-size:22px;font-weight:700;margin:12px 14px 8px;color:#111}
.post h3.hl{color:var(--brand)}
.post p{font-size:13px;line-height:21px;color:#555;margin:0 40px 0 14px}
.dots{top:2566px;left:570px;display:flex;gap:8px}
.dots span{width:13px;height:13px;border:2px solid var(--brand);border-radius:50%}
.dots span.on{background:var(--brand)}

.contact{left:0;top:2767px;width:1200px;height:524px;background:linear-gradient(150deg,#1d4a8a 0%,#3f78b9 30%,#a9c6e6 52%,#eef3f9 68%,#c7d8ec 80%,#2f5d99 100%)}
.field{left:575px;width:475px;border-bottom:2px solid var(--brand);font-size:14px;font-weight:500;color:#222;padding-bottom:4px}

.partner{top:3460px;height:90px;display:flex;align-items:center;justify-content:center;font-weight:700;font-size:27px;color:var(--brand);white-space:nowrap}

.footer{left:0;top:3553px;width:1200px;height:346px;background:var(--footer);color:var(--white)}
.footer h4{color:var(--brand);font-size:15px;font-weight:700;margin-bottom:14px}
.footer li{list-style:none;font-size:13px;margin-bottom:19px}
.fcol{position:absolute;top:38px;font-size:13px;line-height:18px}
</style>
</head>
<body>

<div class="abs topbar">Welcome To Our Website
  <div class="social"><span class="dot"></span><span class="dot"></span><span class="dot"></span></div>
</div>

<header class="abs header">
  <div class="abs brand">
    <div class="mark"></div>
    <div class="name">Keystone Forma</div>
    <div class="tag">Building with peace of mind</div>
  </div>
  <nav class="abs nav">
    <span class="on">HOME</span><span>ABOUT</span><span>SERVICES</span><span>PORTFOLIO</span><span>BLOG</span><span>CONTACT</span>
  </nav>
</header>

<section class="abs hero" role="img" aria-label="Photo of a large empty industrial warehouse interior with steel roof trusses">
  <h2>WELCOME FOR</h2>
  <h1>KEYSTONE FORMA</h1>
</section>

<div class="abs slide-img" style="left:87px;width:342px;background:linear-gradient(135deg,#b98c5c 0%,#e8e2d6 45%,#dfe7f0 70%,#9cb6d2 100%)" role="img" aria-label="Miniature house frame model with workers on architectural plans"></div>
<div class="abs service-card">
  <svg width="120" height="86" viewBox="0 0 120 86" fill="none" stroke="#fff" stroke-width="5" stroke-linejoin="round">
    <path d="M12 44 L48 12 L84 44"/><path d="M22 36 V74 H62"/><circle cx="84" cy="58" r="22"/><path d="M84 46 V58 H94"/>
  </svg>
  <h3>24–HR SERVICE</h3>
  <p>Lorem ipsum dolor sit amet, consectetur adipisicing elit, sed do eiusmod tempor incididunt ut labore et dolore magna aliqua.</p>
</div>
<div class="abs slide-img" style="left:770px;width:343px;background:linear-gradient(135deg,#3f76b8 0%,#c6d2dc 40%,#8e969e 70%,#4d5a66 100%)" role="img" aria-label="Engineers in hard hats reviewing plans on site"></div>
<div class="abs arrow" style="left:87px"><svg width="12" height="16" viewBox="0 0 12 16"><path d="M9 2 L3 8 L9 14" stroke="#fff" stroke-width="3" fill="none"/></svg></div>
<div class="abs arrow" style="left:1083px"><svg width="12" height="16" viewBox="0 0 12 16"><path d="M3 2 L9 8 L3 14" stroke="#fff" stroke-width="3" fill="none"/></svg></div>

<h2 class="abs section-title" style="left:61px;top:977px">ABOUT US</h2>
<div class="abs about-text">
  <p>Lorem ipsum dolor sit amet, consectetur adipisicing elit, sed do eiusmod tempor incididunt ut labore et dolore magna aliqua. Ut enim ad minim veniam, quis nostrud exercitation ullamco laboris nisi ut aliquip ex ea commodo consequat. Duis aute irure dolor in reprehenderit in voluptate velit esse cillum dolore eu fugiat nulla pariatur.</p>
  <p>Excepteur sint occaecat cupidatat non proident, sunt in culpa qui officia deserunt mollit anim id est laborum. Sed ut perspiciatis unde omnis iste natus error sit voluptatem accusantium doloremque laudantium, totam rem aperiam, eaque ipsa quae ab illo inventore veritatis et quasi architecto beatae vitae dicta sunt explicabo.</p>
</div>
<div class="abs btn" style="left:61px;top:1331px;width:133px;height:43px">READ MORE</div>
<div class="abs" style="left:610px;top:991px;width:590px;height:382px;background:linear-gradient(160deg,#f2eee8 0%,#d9cfc2 35%,#a9825c 65%,#6e5440 100%)" role="img" aria-label="Bright dining room with wooden table and vaulted timber ceiling"></div>

<h2 class="abs section-title center" style="top:1450px">PORTFOLIO</h2>
<div class="abs grid">
  <div class="cell" style="background:linear-gradient(160deg,#6f9ad0 0%,#c9d6e4 55%,#8f9aa6 100%)" role="img" aria-label="Modern glass office building"></div>
  <div class="cell hosp">
    <svg width="90" height="80" viewBox="0 0 90 80" fill="none" stroke="#fff" stroke-width="4"><rect x="10" y="14" width="40" height="62"/><rect x="50" y="38" width="30" height="38"/><rect x="18" y="4" width="24" height="10"/><path d="M20 26h8M34 26h8M20 40h8M34 40h8M20 54h8M34 54h8M58 50h14M58 62h14"/></svg>
    <h3>HOSPITALITY</h3>
    <p>Excepteur sint occaecat cupidatat non proident, sunt in culpa qui officia deserunt mollit anim id est laborum.</p>
  </div>
  <div class="cell" style="background:linear-gradient(135deg,#f4f2ef 0%,#d8d2ca 55%,#b8a58a 100%)" role="img" aria-label="Open plan office interior with pendant lamps"></div>
  <div class="cell" style="background:linear-gradient(180deg,#8fb4e0 0%,#b98a62 40%,#6f8c4a 62%,#4f9a32 100%)" role="img" aria-label="School building with green lawn"></div>
  <div class="cell" style="background:linear-gradient(135deg,#5a4a33 0%,#c9a86a 45%,#9d8a6a 70%,#4a3d2c 100%)" role="img" aria-label="Shopping mall escalators"></div>
  <div class="cell" style="background:linear-gradient(180deg,#9cc9ee 0%,#e8dcc0 40%,#3aa0c8 65%,#8a5a36 100%)" role="img" aria-label="Resort hotel with pool and sun loungers"></div>
  <div class="cell" style="background:linear-gradient(135deg,#e8ebef 0%,#b9c3cc 45%,#c6884a 75%,#d3a24a 100%)" role="img" aria-label="Colourful modern office interior"></div>
  <div class="cell" style="background:linear-gradient(180deg,#6f8fb8 0%,#3c4554 50%,#8a6a3e 70%,#4f6a3a 100%)" role="img" aria-label="Modern two-storey house at dusk"></div>
</div>
<div class="abs btn" style="left:534px;top:2058px;width:132px;height:42px">VIEW ALL</div>

<h2 class="abs section-title center" style="top:2180px">BLOG POST</h2>
<article class="abs post" style="left:87px">
  <div class="ph" style="background:linear-gradient(160deg,#e4e1dc 0%,#c9603a 35%,#8d3a22 75%,#6b2c1a 100%)" role="img" aria-label="Bricklayer laying red bricks"></div>
  <h3>Technology has helped</h3>
  <p>Lorem ipsum dolor sit amet, consectetur adipisicing elit, sed do eiusmod tempor incididunt ut labore et dolore magna aliqua.</p>
</article>
<article class="abs post" style="left:444px">
  <div class="ph" style="background:linear-gradient(135deg,#d8c4a4 0%,#8a7256 45%,#4e4032 75%,#c9b79c 100%)" role="img" aria-label="Two workers inspecting a building under construction"></div>
  <h3 class="hl">Technology has helped</h3>
  <p>Lorem ipsum dolor sit amet, consectetur adipisicing elit, sed do eiusmod tempor incididunt ut labore et dolore magna aliqua.</p>
</article>
<article class="abs post" style="left:800px">
  <div class="ph" style="background:linear-gradient(160deg,#f0d58a 0%,#c9a24a 30%,#8d9296 60%,#4e5256 100%)" role="img" aria-label="Engineers working on plans with a hard hat and level"></div>
  <h3>Technology has helped</h3>
  <p>Lorem ipsum dolor sit amet, consectetur adipisicing elit, sed do eiusmod tempor incididunt ut labore et dolore magna aliqua.</p>
</article>
<div class="abs dots"><span></span><span class="on"></span><span></span></div>
<div class="abs btn" style="left:533px;top:2634px;width:132px;height:44px">VIEW ALL</div>

<section class="abs contact" role="img" aria-label="Curved glass skyscraper facade against a blue sky">
  <h2 class="abs section-title" style="left:575px;top:45px">CONTACT US</h2>
  <div class="abs field" style="top:108px">NAME</div>
  <div class="abs field" style="top:147px">EMAIL</div>
  <div class="abs field" style="top:185px">MOBILE NUMBER</div>
  <div class="abs field" style="top:228px;height:44px">MESSAGE</div>
  <div class="abs btn" style="left:919px;top:302px;width:131px;height:42px">SEND DATA</div>
</section>

<h2 class="abs section-title center" style="top:3370px">OUR PARTNERS</h2>
<div class="abs partner" style="left:135px;width:92px"><div style="width:88px;height:88px;border-radius:50%;border:4px solid #222"></div></div>
<div class="abs partner" style="left:285px;width:240px">Fernleaf Pharmacy</div>
<div class="abs partner" style="left:560px;width:210px">Riverside Athletics</div>
<div class="abs partner" style="left:800px;width:270px">Numeria Learning</div>

<footer class="abs footer">
  <div class="abs" style="left:175px;top:32px;width:116px;height:116px;border-radius:50%;background:var(--white)"></div>
  <p class="abs" style="left:80px;top:162px;width:305px;text-align:center;font-size:14px;line-height:21px">Lorem ipsum dolor sit amet, consectetur adipisicing elit, sed do eiusmod tempor incididunt ut labore et dolore magna aliqua.</p>
  <div class="fcol" style="left:459px"><h4>QUICK LINKS</h4>
    <ul><li>Home</li><li>About</li><li>Services</li><li>Portfolio</li><li>Blog</li><li>Contact</li></ul></div>
  <div class="fcol" style="left:608px;width:210px"><h4>CONTACT US</h4>
    <p>Orion 12 Str. 10458, Marousi Athens, Greece</p>
    <p style="margin-top:14px">+30-2100000123 (landline)</p>
    <p style="margin-top:14px">www.keystoneforma.example</p></div>
  <div class="fcol" style="left:843px"><h4>NEWSLETTER</h4>
    <div style="display:flex"><div style="width:225px;height:40px;background:#fff;color:#555;font-size:11px;padding:12px 8px">ENTER EMAIL</div>
      <div style="width:44px;height:40px;background:var(--brand);display:flex;align-items:center;justify-content:center"><svg width="20" height="20" viewBox="0 0 20 20" fill="none" stroke="#fff" stroke-width="3"><circle cx="8" cy="8" r="6"/><path d="M12.5 12.5 L18 18"/></svg></div></div>
    <div style="display:flex;gap:14px;margin:22px 0 0 82px"><span class="dot" style="background:var(--brand);width:24px;height:24px"></span><span class="dot" style="background:var(--brand);width:24px;height:24px"></span><span class="dot" style="background:var(--brand);width:24px;height:24px"></span></div>
  </div>
  <div class="abs" style="left:87px;top:294px;width:1026px;height:1px;background:var(--divider)"></div>
  <p class="abs center" style="top:314px;font-size:14px">© 2020. <span style="color:var(--brand)">Keystone Forma</span> All Right Reserved</p>
</footer>

</body>
</html>
```